Home Security Company Business Card

Looking for a eye catching business card that is non traditional and stands out but yet still looks professional. It should include all the pertinent information such as name, title, address, telephone, e-mail, website address should definitely stand out and then finally the logo.

Target Market(s)

Residential and Commercial accounts mostly upscale accounts

Industry/Entity Type

Security

Contact Information for Business Card

Name
Title
Address
Office #
Cell #
E-mail
Website

Font styles to use
Serif
Sans Serif

Requirements
Must have
• Logo, two sided color configuration
Nice to have
• You decide
Should not have
• There really aren't any.

```html
<!DOCTYPE html>
<html lang="en">
<head>
<meta charset="utf-8">
<title>Harborline Security Systems – Business Card</title>
<link rel="stylesheet" href="https://fonts.googleapis.com/css2?family=Tinos&family=Source+Sans+3:wght@400;600&display=swap">
<style>
  :root {
    --stage: #000000;
    --card-white: #ffffff;
    --card-red: #7b1517;
    --brand-red: #7d1a16;
    --gold: #e0a23a;
    --gold-light: #f2c45a;
    --ink: #2b2b2b;
  }
  html, body {
    margin: 0;
    padding: 0;
    width: 1200px;
    height: 900px;
    overflow: hidden;
    background: var(--stage);
  }
  .canvas {
    position: relative;
    width: 1200px;
    height: 900px;
    background: var(--stage);
  }
  .card {
    position: absolute;
    top: 275px;
    width: 477px;
    height: 293px;
    box-sizing: border-box;
  }
  .card-front {
    left: 120px;
    background: var(--card-white);
    border-radius: 0 52px 0 52px;
  }
  .card-back {
    left: 606px;
    top: 274px;
    background: var(--card-red);
    border-radius: 52px 0 52px 0;
  }
  .brand {
    position: absolute;
    left: 22px;
    top: 64px;
    display: flex;
    align-items: center;
    gap: 12px;
    font-family: "Tinos", "Times New Roman", serif;
    font-weight: 400;
    color: var(--brand-red);
  }
  .brand-dot {
    width: 40px;
    height: 40px;
    border-radius: 50%;
    background: var(--gold);
    flex: none;
  }
  .brand-name {
    font-size: 25px;
    line-height: 1;
    letter-spacing: 0.2px;
  }
  .brand-name small {
    display: block;
    font-size: 12.5px;
    margin-top: 3px;
  }
  .contact {
    position: absolute;
    right: 22px;
    top: 108px;
    text-align: right;
    font-family: "Source Sans 3", "Helvetica", sans-serif;
    color: var(--ink);
  }
  .person-name {
    font-size: 19px;
    font-weight: 600;
    color: var(--brand-red);
    margin: 0;
    line-height: 1.2;
  }
  .person-title {
    font-size: 13px;
    color: var(--gold);
    margin: 2px 0 10px;
  }
  .address {
    font-size: 13px;
    line-height: 16px;
    margin: 0 0 13px;
    padding-right: 0;
  }
  .lines {
    list-style: none;
    margin: 0;
    padding: 0;
    font-size: 13px;
    line-height: 17.5px;
  }
  .lines li {
    display: flex;
    justify-content: flex-end;
    align-items: center;
    gap: 8px;
  }
  .lines svg {
    width: 10px;
    height: 10px;
    fill: var(--brand-red);
    stroke: var(--brand-red);
  }
  .address span { display: block; padding-right: 18px; }
  .back-brand {
    position: absolute;
    inset: 0;
    display: flex;
    flex-direction: column;
    align-items: center;
    justify-content: center;
    gap: 16px;
    font-family: "Tinos", "Times New Roman", serif;
    font-weight: 400;
    color: var(--gold-light);
    font-size: 28px;
  }
  .back-brand .brand-dot {
    width: 90px;
    height: 90px;
    background: var(--gold);
  }
</style>
</head>
<body>
<div class="canvas">
  <section class="card card-front">
    <div class="brand">
      <span class="brand-dot"></span>
      <div class="brand-name">HARBORLINE<small>SECURITY SYSTEMS INC.</small></div>
    </div>
    <div class="contact">
      <h1 class="person-name">Jonathan Smith</h1>
      <p class="person-title">Managing Director</p>
      <p class="address"><span>1234, Address Goes Here</span><span>Country Name, 123456</span></p>
      <ul class="lines">
        <li>123-456-7890
          <svg viewBox="0 0 10 10" aria-hidden="true"><rect x="2.5" y="0.5" width="5" height="9" rx="1" fill="none" stroke-width="1.2"/><rect x="4.3" y="7.6" width="1.4" height="0.8" stroke="none"/></svg>
        </li>
        <li>123-456-7890
          <svg viewBox="0 0 10 10" aria-hidden="true"><path d="M0.5 3.5 Q5 0 9.5 3.5 L8 4.5 L6.5 3.5 H3.5 L2 4.5 Z" stroke="none"/><rect x="1.5" y="5" width="7" height="4.5" rx="0.8" stroke="none"/></svg>
        </li>
        <li>info@youremail.com
          <svg viewBox="0 0 10 10" aria-hidden="true"><rect x="0.5" y="2" width="9" height="6.5" stroke="none"/><path d="M0.8 2.3 L5 5.8 L9.2 2.3" fill="none" stroke="#ffffff" stroke-width="0.9"/></svg>
        </li>
        <li>www.yourweb.com
          <svg viewBox="0 0 10 10" aria-hidden="true"><path d="M4 6 L6 4 M3.2 5 L1.5 6.7 a1.4 1.4 0 0 0 1.8 1.8 L5 6.8 M6.8 5 L8.5 3.3 a1.4 1.4 0 0 0 -1.8 -1.8 L5 3.2" fill="none" stroke-width="1.1" stroke-linecap="round"/></svg>
        </li>
      </ul>
    </div>
  </section>

  <section class="card card-back">
    <div class="back-brand">
      <span class="brand-dot"></span>
      <span>HARBORLINE</span>
    </div>
  </section>
</div>
</body>
</html>
```